Professional and creative business card design for recruiting service providers

Our company supports German medium-sized companies in filling vacancies promptly. For this we use social media marketing and bring our customers into the visibility.

We want a professional but also creative design for our business cards.

Please look at lindqvar-staff.de to get an impression of our CI.

Target Market(s)

Small and medium-sized companies in Germany from the industry

Industry/Entity Type

Industrie, Handwerk

Contact Information for Business Card

Name, Position, Telefonnummer, Email, Website

Colors
EE7325
F08F49
F5BC92
FAE3D3
FDF4ED

Requirements
Must have
• A picture of the employee and in the style of www.lindqvar-staff.de

```html
<!DOCTYPE html>
<html lang="en">
<head>
<meta charset="utf-8">
<title>Lindqvar &amp; Staff – Business Card</title>
<link href="https://fonts.googleapis.com/css2?family=Jost:wght@500;600&family=Arimo:wght@400&display=swap" rel="stylesheet">
<style>
  :root {
    --orange: #EE7325;
    --orange-soft: #F08F49;
    --ink: #141414;
    --card-black: #1a1a1a;
    --logo-shade: #3a3a3a;
    --paper: #ffffff;
    --stage: #2b2b2b;
    --photo-wall: #d9d6d4;
    --photo-suit: #4a4748;
  }
  * { box-sizing: border-box; margin: 0; padding: 0; }
  html, body { width: 1200px; height: 1040px; overflow: hidden; }
  body {
    background: var(--stage);
    position: relative;
    font-family: "Arimo", Arial, sans-serif;
  }
  .card {
    position: absolute;
    left: 270px;
    width: 660px;
    height: 376px;
    border-radius: 0 64px 0 64px;
    overflow: hidden;
    box-shadow: 0 14px 30px rgba(0,0,0,0.45);
  }
  /* Back side */
  .card-back {
    top: 110px;
    background: var(--card-black);
    display: flex;
    align-items: center;
    justify-content: center;
  }
  .back-brand {
    display: flex;
    align-items: center;
    gap: 18px;
    font-family: "Jost", sans-serif;
    font-weight: 600;
    font-size: 40px;
    letter-spacing: 4px;
    color: var(--logo-shade);
    text-transform: uppercase;
  }
  .back-brand .brand-square {
    width: 34px; height: 34px;
    background: var(--logo-shade);
  }
  /* Front side */
  .card-front {
    top: 556px;
    background: var(--paper);
    display: flex;
  }
  .employee-photo {
    width: 46%;
    height: 100%;
    background: linear-gradient(180deg, var(--photo-wall) 0%, #c9c4c1 45%, var(--photo-suit) 46%, #3a3839 86%, #b98d62 87%, #c79b6e 100%);
  }
  .front-content {
    flex: 1;
    padding: 70px 28px 0 30px;
  }
  .front-brand {
    display: flex;
    align-items: center;
    gap: 14px;
    font-family: "Jost", sans-serif;
    font-weight: 600;
    font-size: 26px;
    line-height: 1.05;
    letter-spacing: 2.5px;
    color: var(--ink);
    text-transform: uppercase;
    margin-left: 18px;
  }
  .front-brand .brand-square {
    width: 52px; height: 52px;
    background: var(--orange);
    flex: none;
  }
  .person { margin-top: 46px; }
  .person-name {
    font-family: "Jost", sans-serif;
    font-weight: 600;
    font-size: 25px;
    letter-spacing: 1px;
    color: var(--orange);
    text-transform: uppercase;
    line-height: 1;
  }
  .person-role {
    font-size: 17px;
    color: var(--ink);
    margin-top: 2px;
  }
  .contact-list { list-style: none; margin-top: 16px; }
  .contact-list li {
    display: flex;
    align-items: center;
    gap: 9px;
    font-size: 17px;
    color: var(--ink);
    line-height: 1.5;
  }
  .contact-list svg { width: 17px; height: 17px; flex: none; }
  .accent { color: var(--orange); }
</style>
</head>
<body>
  <section class="card card-back" aria-label="Card back">
    <div class="back-brand"><span class="brand-square"></span>Lindqvar &amp; Staff</div>
  </section>

  <section class="card card-front" aria-label="Card front">
    <div class="employee-photo" role="img" aria-label="Portrait photo of the employee in a dark suit seated at a desk in an office"></div>
    <div class="front-content">
      <div class="front-brand"><span class="brand-square"></span><span>Lindqvar<br>&amp; Staff</span></div>
      <div class="person">
        <h1 class="person-name">Jonas Weller</h1>
        <p class="person-role">Managing Director</p>
      </div>
      <ul class="contact-list">
        <li>
          <svg viewBox="0 0 24 24" aria-hidden="true"><path fill="var(--orange)" d="M6.6 10.8a15 15 0 0 0 6.6 6.6l2.2-2.2a1 1 0 0 1 1-.25 11.4 11.4 0 0 0 3.6.57 1 1 0 0 1 1 1V20a1 1 0 0 1-1 1A17 17 0 0 1 3 4a1 1 0 0 1 1-1h3.5a1 1 0 0 1 1 1c0 1.25.2 2.45.57 3.57a1 1 0 0 1-.25 1z"/></svg>
          040-987 654 321
        </li>
        <li>
          <svg viewBox="0 0 24 24" aria-hidden="true"><rect x="2" y="5" width="20" height="14" fill="var(--orange)"/><path d="M2 5l10 8 10-8" fill="none" stroke="#fff" stroke-width="1.6"/></svg>
          info@lindqvar-staff.de
        </li>
        <li>
          <svg viewBox="0 0 24 24" aria-hidden="true"><g fill="none" stroke="var(--orange)" stroke-width="1.8"><circle cx="12" cy="12" r="9.5"/><ellipse cx="12" cy="12" rx="4" ry="9.5"/><path d="M2.5 12h19M4 7h16M4 17h16"/></g></svg>
          <span>www.<span class="accent">lindqvar-staff</span>.de</span>
        </li>
      </ul>
    </div>
  </section>
</body>
</html>
```